New corporate stationery design for UK train leasing company

In advance of an office move later this year we are looking to redesign all our corporate stationery (business cards, letterhead, compliment slips, envelopes etc) as well as small branded items (such as mouse mats, drink mats, etc).

We wish to keep the same logo and corporate colours but are looking for a modern, fresh look that will tie in our stationery more with the look of our website and our PowerPoint template. We have a strapline, "Rail People, Real Expertise" that we would like to incorporate into the stationery design and also need to include a "TOVEC" logo on the bottom of the letterhead/compliment slips. We have two offices so will need letterhead and compliment slips with both addresses.

The files attached include different versions of our logo (the main one is the black with green halo, file 1 or 3), our brand guidelines summary (including Pantone colours), the TOVEC logo and PowerPoint template.

More information about the business can be found at www.copperlinefleet.co.uk.

If you have any questions please let me know.

I look forward to seeing the designs!
Regards
Harriet

Main audience are train operators, rail industry suppliers, passenger transport groups, government and other political organisations, financiers/lenders.

Business

```html
<!DOCTYPE html>
<html lang="en">
<head>
<meta charset="utf-8">
<title>Copperline Fleet – Stationery Set</title>
<link href="https://fonts.googleapis.com/css2?family=Open+Sans:wght@400;600;700&display=swap" rel="stylesheet">
<style>
  :root {
    --teal: #1a9e8f;
    --ink: #4a4a4a;
    --text: #555555;
    --paper: #ffffff;
    --backdrop: #ececec;
    --line: #dcdcdc;
  }
  * { box-sizing: border-box; margin: 0; padding: 0; }
  html, body { width: 1200px; height: 937px; overflow: hidden; }
  body {
    background: var(--backdrop);
    font-family: "Open Sans", Arial, sans-serif;
    color: var(--text);
    position: relative;
  }
  .sheet { position: absolute; background: var(--paper); overflow: hidden; }

  /* brand name lockup */
  .brand { display: flex; align-items: center; gap: 6px; color: var(--ink); font-weight: 400; letter-spacing: -0.01em; line-height: 1; white-space: nowrap; }
  .brand .dot { border-radius: 50%; background: var(--teal); flex: none; }

  /* letterhead */
  .letterhead { left: 185px; top: 66px; width: 388px; height: 546px; }
  .letterhead .brand { position: absolute; left: 18px; top: 26px; font-size: 23px; }
  .letterhead .brand .dot { width: 9px; height: 9px; }
  .contact-list { position: absolute; right: 18px; top: 23px; list-style: none; font-size: 6.5px; color: var(--text); }
  .contact-list li { display: flex; align-items: center; gap: 4px; height: 11px; }
  .contact-list .ico { width: 7px; height: 7px; border-radius: 50%; background: var(--teal); flex: none; }
  .letter { position: absolute; left: 36px; top: 140px; width: 300px; font-size: 5.6px; line-height: 1.45; color: #666; }
  .letter p { margin-bottom: 8px; }
  .letter .salute { font-weight: 700; color: #444; margin-bottom: 0; }
  .letter .gap { margin-bottom: 16px; }
  .signature { display: block; width: 26px; height: 14px; margin: 4px 0 6px; background: linear-gradient(90deg, #cfcfcf, #e8e8e8); border-radius: 2px; }
  .letter .signer { font-weight: 700; color: #444; margin-bottom: 0; }
  .footer-bar { position: absolute; left: 6px; right: 0; top: 506px; height: 12px; }
  .footer-bar .address-tab { position: absolute; left: 0; top: 0; height: 12px; width: 116px; background: var(--ink); color: #fff; font-size: 5.2px; font-weight: 600; line-height: 12px; padding-left: 10px; clip-path: polygon(4% 0, 100% 0, 100% 100%, 0 100%); }
  .footer-bar .web-tab { position: absolute; left: 116px; top: 0; height: 12px; width: 72px; background: var(--teal); color: #fff; font-size: 5.2px; line-height: 12px; padding-left: 10px; clip-path: polygon(0 0, 88% 0, 100% 100%, 0 100%); }
  .footer-bar .rule { position: absolute; left: 180px; right: 0; top: 10px; height: 2px; background: var(--ink); }
  .base-stripe { position: absolute; left: 0; right: 0; bottom: 0; height: 10px; background: var(--ink); }

  /* cover sheet */
  .cover { left: 636px; top: 40px; width: 458px; height: 578px; }
  .cover .brand { position: absolute; left: 58px; top: 232px; font-size: 44px; gap: 12px; }
  .cover .brand .dot { width: 22px; height: 22px; }
  .cover-footer { position: absolute; left: 14px; right: 10px; top: 532px; height: 16px; }
  .cover-footer .web-tab { position: absolute; left: 0; top: 0; height: 16px; width: 138px; border-bottom: 2px solid var(--teal); color: var(--teal); font-size: 8px; letter-spacing: 0.12em; line-height: 14px; padding-left: 22px; }
  .cover-footer .rule { position: absolute; left: 132px; right: 0; top: 14px; height: 2px; background: var(--teal); }
  .cover .base-stripe { height: 13px; }

  /* business cards */
  .card { left: 45px; width: 178px; height: 98px; border-radius: 5px; }
  .card-front { top: 658px; }
  .card-front .brand { position: absolute; left: 8px; top: 11px; font-size: 15px; gap: 4px; }
  .card-front .brand .dot { width: 6px; height: 6px; }
  .name-bar { position: absolute; left: 0; top: 40px; width: 178px; height: 10px; }
  .name-bar .name { position: absolute; left: 0; top: 0; width: 80px; height: 10px; background: var(--ink); color: #fff; font-size: 5.6px; font-weight: 700; line-height: 10px; padding-left: 8px; }
  .name-bar .role { position: absolute; left: 80px; top: 0; width: 40px; height: 10px; background: var(--teal); color: #fff; font-size: 5px; line-height: 10px; padding-left: 5px; clip-path: polygon(0 0, 84% 0, 100% 100%, 0 100%); }
  .name-bar .rule { position: absolute; left: 112px; right: 0; top: 8px; height: 2px; background: var(--ink); }
  .card-address { position: absolute; left: 16px; top: 55px; font-size: 4.6px; line-height: 1.35; color: #666; width: 60px; }
  .card-web { position: absolute; left: 16px; top: 78px; font-size: 4.6px; color: #666; }
  .card-front .contact-list { left: 88px; right: auto; top: 53px; font-size: 4.6px; }
  .card-front .contact-list li { height: 7.2px; gap: 3px; }
  .card-front .contact-list .ico { width: 5px; height: 5px; }
  .card-front .base-stripe { height: 6px; }
  .card-back { top: 785px; height: 100px; background: var(--ink); }
  .card-back .brand { position: absolute; left: 34px; top: 38px; font-size: 17px; color: #fff; gap: 5px; }
  .card-back .brand .dot { width: 7px; height: 7px; }

  /* envelopes */
  .envelope-front { left: 264px; top: 671px; width: 435px; height: 210px; }
  .envelope-front .brand { position: absolute; left: 15px; top: 22px; font-size: 22px; gap: 5px; }
  .envelope-front .brand .dot { width: 8px; height: 8px; }
  .envelope-front .return-address { position: absolute; left: 15px; top: 53px; font-size: 7.4px; color: #444; }
  .envelope-back { left: 737px; top: 671px; width: 432px; height: 209px; }
  .flap { position: absolute; left: 0; top: 0; width: 100%; height: 72px; background: var(--ink); border-radius: 0 0 40px 40px; }
  .flap .web { position: absolute; left: 0; right: 0; top: 28px; text-align: center; color: #fff; font-size: 13px; letter-spacing: 0.16em; }
  .flap .web b { font-weight: 700; }
</style>
</head>
<body>

  <!-- Letterhead -->
  <section class="sheet letterhead">
    <div class="brand"><span>copperline fleet</span><span class="dot"></span></div>
    <ul class="contact-list">
      <li><span class="ico"></span>012 345 6789</li>
      <li><span class="ico"></span>012 345 6789</li>
      <li><span class="ico"></span>012 345 6789</li>
      <li><span class="ico"></span>urname@email.com</li>
    </ul>
    <div class="letter">
      <p>July 2, 2012</p>
      <p class="salute">Dear Sir,</p>
      <p>ABC Building, def St., Country Name</p>
      <p class="gap">Thank you for your continued partnership with our fleet team. This letter confirms the arrangements discussed at our recent meeting regarding the leasing schedule for the coming year. Our engineers will review each unit before delivery and share a full condition report with your operations staff. Please contact our office if any details need to be adjusted before the agreement is finalised.</p>
      <p class="gap">We will also send updated maintenance records and a revised timetable for the depot handover next month.</p>
      <p>Our finance team has prepared the quarterly statement and will forward it to your accounts department this week. Should you wish to discuss extending the current terms, we would be glad to arrange a visit to your offices at a convenient time. We value the trust you place in our people and look forward to working together.</p>
      <p>Best Regards,</p>
      <span class="signature" role="img" aria-label="Handwritten signature of the director"></span>
      <p class="signer">Daniel Reeve</p>
      <p style="margin-bottom:0">Director</p>
      <p>ABC Building, def St., Country Name</p>
    </div>
    <div class="footer-bar">
      <div class="address-tab">12 Station Court, Level 4, Derby</div>
      <div class="web-tab">www.YourWebsite.com</div>
      <div class="rule"></div>
    </div>
    <div class="base-stripe"></div>
  </section>

  <!-- Cover sheet -->
  <section class="sheet cover">
    <div class="brand"><span>copperline fleet</span><span class="dot"></span></div>
    <div class="cover-footer">
      <div class="web-tab">www.YourWebsite.com</div>
      <div class="rule"></div>
    </div>
    <div class="base-stripe"></div>
  </section>

  <!-- Business card, front -->
  <section class="sheet card card-front">
    <div class="brand"><span>copperline fleet</span><span class="dot"></span></div>
    <div class="name-bar">
      <div class="name">MARTIN HOLLOWAY</div>
      <div class="role">Manager</div>
      <div class="rule"></div>
    </div>
    <div class="card-address">12 Station Court, Level 4, Derby</div>
    <div class="card-web">www.YourWebsite.com</div>
    <ul class="contact-list">
      <li><span class="ico"></span>012 345 6789</li>
      <li><span class="ico"></span>012 345 6789</li>
      <li><span class="ico"></span>012 345 6789</li>
      <li><span class="ico"></span>urname@email.com</li>
    </ul>
    <div class="base-stripe"></div>
  </section>

  <!-- Business card, back -->
  <section class="sheet card card-back">
    <div class="brand"><span>copperline fleet</span><span class="dot"></span></div>
  </section>

  <!-- Envelope, front -->
  <section class="sheet envelope-front">
    <div class="brand"><span>copperline fleet</span><span class="dot"></span></div>
    <p class="return-address">12 Station Court, Level 4, Derby</p>
  </section>

  <!-- Envelope, back -->
  <section class="sheet envelope-back">
    <div class="flap">
      <p class="web">www.<b>YourWebsite</b>.com</p>
    </div>
  </section>

</body>
</html>
```